digger and truck hire

this is a new business - Digger and Truck
we would like to include the attached photo of the digger and truck - as the truck is red and the digger is green
maybe either black or white lettering which ever suits

Industry/Entity Type

Business

Contact Information for Business Card

RDL - Brodie's 2.5t Mini Digger and 7t Tip Truck -Hire, full attachments, augers, trenching, site preparation, small aggregate deliveries
Phone 0218365904
brodie.rdl@fernmail.co.nz

```html
<!DOCTYPE html>
<html lang="en">
<head>
<meta charset="utf-8">
<title>RDL – Digger and Truck Hire Business Card</title>
<link href="https://fonts.googleapis.com/css2?family=Bebas+Neue&display=swap" rel="stylesheet">
<style>
  :root {
    --page-bg: #2a2a2c;
    --brand-red: #cc1a20;
    --brand-red-dark: #8e0f14;
    --brand-red-light: #e0383d;
    --ink: #111111;
    --paper: #ffffff;
    --steel: #b9bcc0;
    --steel-dark: #6f7479;
    --digger-green: #5f8f4a;
    --truck-orange: #d8552e;
  }
  * { margin: 0; padding: 0; box-sizing: border-box; }
  html, body {
    width: 1200px;
    height: 800px;
    overflow: hidden;
    background: var(--page-bg);
  }
  body {
    position: relative;
    font-family: "Bebas Neue", "Arial Narrow", sans-serif;
  }
  .business-card {
    position: absolute;
    left: 75px;
    top: 100px;
    width: 1050px;
    height: 600px;
    overflow: hidden;
    background: var(--paper);
  }
  .equipment-photo {
    position: absolute;
    inset: 0;
    background:
      linear-gradient(180deg, rgba(255,255,255,0.35) 0%, rgba(255,255,255,0) 40%),
      linear-gradient(100deg,
        var(--steel) 0%,
        var(--steel-dark) 22%,
        var(--digger-green) 34%,
        var(--steel-dark) 48%,
        var(--truck-orange) 70%,
        #c94a2a 85%,
        var(--steel) 100%);
    opacity: 0.85;
  }
  .brand-name {
    position: absolute;
    left: 250px;
    top: 40px;
    font-size: 230px;
    line-height: 1;
    letter-spacing: 4px;
    color: var(--brand-red);
  }
  .tagline-banner {
    position: absolute;
    left: 255px;
    top: 245px;
    padding: 4px 18px 0;
    height: 38px;
    background: linear-gradient(180deg, var(--brand-red-light), var(--brand-red-dark));
    color: var(--paper);
    font-size: 30px;
    line-height: 36px;
    letter-spacing: 1px;
    white-space: nowrap;
  }
  .services-strip {
    position: absolute;
    left: 0;
    right: 0;
    top: 295px;
    height: 44px;
    padding-left: 70px;
    background: rgba(255,255,255,0.78);
    color: var(--ink);
    font-size: 25px;
    line-height: 46px;
    letter-spacing: 0.5px;
    white-space: nowrap;
  }
  .contact-band {
    position: absolute;
    left: 0;
    right: 0;
    top: 339px;
    height: 176px;
    background: linear-gradient(180deg, var(--brand-red-light) 0%, var(--brand-red) 45%, var(--brand-red-dark) 100%);
    border-top: 4px solid var(--steel);
    border-bottom: 4px solid var(--steel);
  }
  .contact-line {
    position: absolute;
    display: flex;
    align-items: center;
    gap: 16px;
    color: var(--paper);
    white-space: nowrap;
  }
  .contact-line svg { fill: var(--paper); flex: none; }
  .contact-phone {
    left: 430px;
    top: 18px;
    font-size: 58px;
    line-height: 1;
  }
  .contact-email {
    left: 290px;
    top: 92px;
    font-size: 64px;
    line-height: 1;
  }
</style>
</head>
<body>
  <main class="business-card">
    <div class="equipment-photo" role="img" aria-label="Photo of the green 2.5t mini digger loaded on the red 7t tip truck in a yard"></div>

    <div class="brand-name">RDL</div>
    <div class="tagline-banner">Brodie's 2.5t Mini Digger and 7t Tip Truck</div>

    <div class="services-strip">Hire, full attachments, augers, trenching, site preparation, small aggregate deliveries</div>

    <section class="contact-band">
      <div class="contact-line contact-phone">
        <svg width="44" height="44" viewBox="0 0 24 24" aria-hidden="true">
          <path d="M6.6 10.8c1.4 2.8 3.8 5.1 6.6 6.6l2.2-2.2c.3-.3.7-.4 1-.2 1.1.4 2.3.6 3.6.6.6 0 1 .4 1 1V20c0 .6-.4 1-1 1C10.6 21 3 13.4 3 4c0-.6.4-1 1-1h3.5c.6 0 1 .4 1 1 0 1.3.2 2.5.6 3.6.1.3 0 .7-.2 1l-2.3 2.2z"/>
        </svg>
        <span>021 836 5904</span>
      </div>
      <div class="contact-line contact-email">
        <svg width="54" height="40" viewBox="0 0 27 20" aria-hidden="true">
          <rect x="1" y="1" width="25" height="18" rx="2" fill="none" stroke="#ffffff" stroke-width="2"/>
          <path d="M2 2l11.5 9L25 2" fill="none" stroke="#ffffff" stroke-width="2"/>
        </svg>
        <span>brodie.rdl@fernmail.co.nz</span>
      </div>
    </section>
  </main>
</body>
</html>
```